Coffee House With Cycling Theme Wants Business Cards

We want to create a business card for a coffee house that has a cycling theme. We expect to use the current logo on one side of the business card and we have been considering adding the words 'COFFEE HOUSE' underneath (see example). For the other side of the business card we want an interesting design with tag-line, address and social media links (the normal business card stuff). See examples provided but we are not fixed on having it exactly as shown, we are very open to great creative ideas. Please note our logo has the initials ‘KR' in orange embedded in the design and this must be retained. However, you can play with the words COFFEE HOUSE as well as use the orange color on the backside of the business card, as you see fit. For an image on the backside of the business card it can be a photo, hand-drawn or whatever but it must visually combine coffee and cycling in some way. The interior of the Coffee House will be reclaimed wood, rustic and have an urban feel to it with cycling artifacts hanging from the walls/ceiling, etc. Finally, it would be beneficial if the business card design elements can be easily used on flyers and other promotional assets. Good luck, we are looking forward to seeing your creative ideas.

Target Market(s)

Coffee lovers and cycling fans

Contact Information for Business Card

See project description.

Colors

Designer to choose colors to be used in the design.

Requirements
Must have
• Must use the current logo provided and combine a coffee and bike theme.
Nice to have
• Orange is used in current logo and could be used as an accent color on the backside of the business card.

```html
<!DOCTYPE html>
<html lang="en">
<head>
<meta charset="utf-8">
<title>KR Coffee House — Business Card</title>
<link href="https://fonts.googleapis.com/css2?family=Oswald:wght@500&family=Work+Sans:wght@400;500&display=swap" rel="stylesheet">
<style>
  :root {
    --bg: #1e1e1e;
    --card: #232323;
    --card-edge: #2c2c2c;
    --ink: #f2f2f2;
    --ink-soft: #bdbdbd;
    --logo: #c9c9c9;
    --accent: #f26a2b;
  }
  * { margin: 0; padding: 0; box-sizing: border-box; }
  html, body { width: 1200px; height: 900px; overflow: hidden; }
  body {
    background: var(--bg);
    font-family: "Work Sans", sans-serif;
    color: var(--ink);
    position: relative;
  }
  .card {
    position: absolute;
    left: 250px;
    width: 700px;
    height: 400px;
    background: linear-gradient(135deg, var(--card) 0%, var(--card-edge) 100%);
    box-shadow: 0 10px 30px rgba(0,0,0,.55);
  }
  .card--front { top: 30px; }
  .card--back { top: 470px; }

  .brand {
    position: absolute;
    inset: 0;
    display: flex;
    align-items: center;
    justify-content: center;
    gap: 18px;
  }
  .brand__dot {
    width: 22px; height: 22px;
    border-radius: 50%;
    background: var(--logo);
  }
  .brand__name {
    font-family: "Work Sans", sans-serif;
    font-weight: 500;
    font-size: 50px;
    letter-spacing: 3px;
    color: var(--logo);
  }

  .person {
    position: absolute;
    top: 120px;
    right: 370px;
    text-align: right;
  }
  .person__name {
    font-family: "Oswald", sans-serif;
    font-weight: 500;
    font-size: 42px;
    line-height: 1;
    letter-spacing: 1px;
    text-transform: uppercase;
    color: var(--accent);
  }
  .person__role {
    margin-top: 6px;
    font-size: 18px;
    color: var(--ink);
  }
  .divider {
    position: absolute;
    left: 350px;
    top: 118px;
    width: 2px;
    height: 68px;
    background: var(--ink);
  }
  .contacts {
    position: absolute;
    left: 372px;
    top: 116px;
    list-style: none;
    font-size: 18px;
    line-height: 25px;
  }
  .contacts li { display: flex; align-items: center; gap: 10px; }
  .contacts svg { width: 13px; height: 13px; flex: none; }

  .footer {
    position: absolute;
    left: 0; right: 0;
    top: 272px;
    text-align: center;
    font-size: 18px;
    line-height: 28px;
  }
  .socials { display: flex; justify-content: center; gap: 30px; }
  .social { display: flex; align-items: center; gap: 10px; }
  .social__square { width: 18px; height: 18px; background: #3b6fd1; border-radius: 2px; }
  .social__circle { width: 18px; height: 18px; background: #d24a7a; border-radius: 50%; }
</style>
</head>
<body>
  <section class="card card--front">
    <div class="brand">
      <span class="brand__dot"></span>
      <span class="brand__name">KR COFFEE HOUSE</span>
    </div>
  </section>

  <section class="card card--back">
    <div class="person">
      <p class="person__name">Daniel Hart</p>
      <p class="person__role">Director</p>
    </div>
    <div class="divider"></div>
    <ul class="contacts">
      <li>
        <svg viewBox="0 0 16 16"><path d="M4 1l3 3-2 2c1 2 3 4 5 5l2-2 3 3-2 3C7 15 1 9 1 3z" fill="var(--accent)"/></svg>
        (555) 014-2290
      </li>
      <li>
        <svg viewBox="0 0 16 16"><rect x="1" y="3" width="14" height="10" fill="none" stroke="var(--accent)" stroke-width="1.6"/><path d="M1 3l7 6 7-6" fill="none" stroke="var(--accent)" stroke-width="1.6"/></svg>
        info@krcoffeehouse.com
      </li>
      <li>
        <svg viewBox="0 0 16 16"><g fill="none" stroke="var(--accent)" stroke-width="1.4"><circle cx="8" cy="8" r="6.5"/><ellipse cx="8" cy="8" rx="3" ry="6.5"/><path d="M1.5 8h13"/></g></svg>
        www.krcoffeehouse.com
      </li>
    </ul>
    <div class="footer">
      <p>52b Mill Lane, Lakeford, NZ, 4410</p>
      <div class="socials">
        <span class="social"><span class="social__square"></span>krcoffeehouse.com</span>
        <span class="social"><span class="social__circle"></span>krcoffeehouse.com</span>
      </div>
    </div>
  </section>
</body>
</html>
```